Brochure for a website accessibility report

This brochure is related to a report that www.qelvantrix.org sell. The report shows the results of an automated audit of a websites accessibility. It shows details of issues found with screen shots, examples of code and provides remediation advice.

The brochure will be a pdf 8.5 inches by 11 inches. It can be anywhere from 6 to 10 pages.

The FlintVue™ name itself should be “Bree Serif” font. The fonts, styles, colors and sizes are up to you.

The images used and logo of the Office of Digital Reachworks and K7P logo are upload

We highlighted in blue page extracts from the report we sell. Do not use the blue highlight, it is merely there to show you where the specific examples of the report we sell are vs the other content in the report. The areas in blue which show the content from the actual report should be shown as an extract of the actual page of the report. You have flexibility to change the layout and the way the content look.

The red square callouts over the blue content are callouts that describe the specific page extracts. We used it as a red callout only so that you would be able to see it. You should change the specific location, look and feel of the callout to be appropriate

Target Market(s)

Marketing and Technical people

Industry/Entity Type

Information Technology

Font styles to use
Sans Serif

Colors

Designer to choose colors to be used in the design.

Requirements
Should not have
• wheelchairs, images of blind people

```html
<!DOCTYPE html>
<html lang="en">
<head>
<meta charset="utf-8">
<title>Office of Digital Reachworks — Brochure for a Website Accessibility Report</title>
<link rel="stylesheet" href="https://fonts.googleapis.com/css2?family=Bree+Serif&family=Raleway:wght@300;600;700&display=swap">
<style>
  :root {
    --bg-top: #8c8c8e;
    --bg-light: #a7a7a9;
    --bg-bottom: #666668;
    --accent-green: #4caf78;
    --ice: #d8eef2;
    --ice-soft: #c3e4ea;
  }
  html, body {
    margin: 0;
    padding: 0;
    width: 927px;
    height: 1200px;
    overflow: hidden;
  }
  .cover {
    position: relative;
    width: 927px;
    height: 1200px;
    overflow: hidden;
    background: var(--bg-top);
  }
  .cover__scene {
    position: absolute;
    inset: 0;
    display: block;
  }
  .cover__year {
    position: absolute;
    left: 724px;
    top: 96px;
    margin: 0;
    font-family: "Raleway", sans-serif;
    font-weight: 700;
    font-size: 47px;
    line-height: 1;
    color: var(--ice-soft);
    letter-spacing: 0.5px;
  }
  .cover__subtitle {
    position: absolute;
    left: 845px;
    top: 104px;
    margin: 0;
    writing-mode: vertical-rl;
    font-family: "Raleway", sans-serif;
    font-weight: 300;
    font-size: 25px;
    line-height: 1;
    color: var(--ice-soft);
    white-space: nowrap;
  }
  .cover__title {
    position: absolute;
    left: 310px;
    top: 778px;
    margin: 0;
    font-family: "Bree Serif", serif;
    font-weight: 400;
    font-size: 66px;
    line-height: 77px;
    color: var(--ice);
    text-transform: uppercase;
    letter-spacing: 0.5px;
  }
  .cover__title span { display: block; }
  .cover__web {
    position: absolute;
    right: 78px;
    top: 1029px;
    margin: 0;
    font-family: "Raleway", sans-serif;
    font-weight: 600;
    font-size: 15px;
    color: var(--ice-soft);
  }
</style>
</head>
<body>
  <main class="cover">
    <svg class="cover__scene" width="927" height="1200" viewBox="0 0 927 1200">
      <defs>
        <linearGradient id="scene-tone" x1="1" y1="0" x2="0.2" y2="1">
          <stop offset="0" stop-color="#a9a9ab"/>
          <stop offset="0.45" stop-color="#8f8f91"/>
          <stop offset="1" stop-color="#616163"/>
        </linearGradient>
      </defs>
      <rect class="cover__photo" width="927" height="1200" fill="url(#scene-tone)" role="img" aria-label="Photo of a laptop with floating translucent dashboard screens showing audit gauges and charts"/>
      <polygon class="cover__accent" points="0,233 237,360 237,1032 0,1112" fill="var(--accent-green)" opacity="0.88"/>
    </svg>

    <p class="cover__year">2019</p>
    <p class="cover__subtitle">Brochure for a Website Accessibility Report</p>

    <h1 class="cover__title">
      <span>Office of</span>
      <span>Digital</span>
      <span>Reachworks</span>
    </h1>

    <p class="cover__web">www.qelvantrix.org</p>
  </main>
</body>
</html>
```